Business Card Design for Occupational Medicine Start Up Company

We need to design a professional business card. We are a healthcare company providing occupational medicine services to blue collar industries. We are professional, efficient and high quality service providers.

Target Market(s)

Blue Collar Industry: Shipbuilding, Ports, Trucking Companies; The Executives and Safety Officers for these companies

Industry/Entity Type

Healthcare

Contact Information for Business Card

Logo, Name, Title, Email, Phone

Other font styles liked:
• Please match our Brand Guide

Requirements
Must have
• Our Company Colors and Logo

```html
<!DOCTYPE html>
<html lang="en">
<head>
<meta charset="utf-8">
<title>CrewSafe Clinics – Business Card</title>
<link rel="stylesheet" href="https://fonts.googleapis.com/css2?family=Montserrat:wght@400;500;600;700&display=swap">
<style>
  :root {
    --stage: #2b2b2d;
    --navy: #2e2f7a;
    --navy-deep: #2a2b6e;
    --indigo: #7a7de0;
    --sky: #2a9fd8;
    --amber: #f0a833;
    --paper: #f6f6f4;
    --ink: #2e2f7a;
  }
  * { box-sizing: border-box; margin: 0; padding: 0; }
  html, body { width: 1200px; height: 1200px; overflow: hidden; }
  body {
    background: var(--stage);
    font-family: "Montserrat", sans-serif;
    position: relative;
  }
  .card {
    position: absolute;
    width: 594px;
    height: 348px;
    border-radius: 22px;
    overflow: hidden;
  }
  /* Front */
  .card-front {
    left: 298px; top: 200px;
    background: var(--navy);
  }
  .front-brand {
    position: absolute;
    left: 0; right: 0; top: 118px;
    display: flex; align-items: center; justify-content: center; gap: 14px;
  }
  .front-brand .dot {
    width: 30px; height: 30px; border-radius: 50%;
    background: var(--indigo);
  }
  .front-brand .name {
    font-size: 34px; font-weight: 700; letter-spacing: 1px;
    color: var(--indigo); text-transform: uppercase;
  }
  .front-url {
    position: absolute; left: 0; right: 0; top: 298px;
    text-align: center; font-size: 15px; font-weight: 500;
    letter-spacing: 1.2px; color: #ffffff;
  }
  .front-url .u-sky { color: var(--sky); }
  .front-url .u-indigo { color: #a7b2f0; }
  .front-url .u-amber { color: var(--amber); }

  /* Back */
  .card-back {
    left: 292px; top: 637px;
    background: var(--paper);
  }
  .stripes { position: absolute; left: 0; top: 0; bottom: 0; }
  .stripe { position: absolute; top: 0; bottom: 0; }
  .stripe-amber { left: 0; width: 13px; background: var(--amber); }
  .stripe-navy { left: 18px; width: 7px; background: var(--navy); }
  .stripe-sky { left: 31px; width: 9px; background: var(--sky); }

  .back-brand {
    position: absolute; left: 72px; top: 48px;
    display: flex; align-items: center; gap: 14px;
  }
  .back-brand .dot {
    width: 40px; height: 40px; border-radius: 50%;
    background: var(--sky);
  }
  .back-brand .name {
    font-size: 32px; font-weight: 700; color: var(--ink);
    text-transform: uppercase; letter-spacing: 0.5px;
  }
  .person { position: absolute; left: 71px; top: 176px; }
  .person-name {
    font-size: 25px; font-weight: 600; color: var(--sky);
    text-transform: uppercase; letter-spacing: 0.3px; line-height: 1;
  }
  .person-title {
    margin-top: 8px; font-size: 15px; font-weight: 500; color: var(--ink);
  }
  .contacts {
    position: absolute; left: 71px; top: 252px;
    list-style: none;
  }
  .contacts li, .address {
    display: flex; align-items: center; gap: 10px;
    font-size: 15.5px; color: var(--ink); height: 21px;
  }
  .contacts svg { width: 14px; height: 14px; flex: none; }
  .address {
    position: absolute; left: 322px; top: 273px;
    align-items: flex-start; height: auto;
  }
  .address svg { width: 14px; height: 16px; margin-top: 2px; flex: none; }
  .address p { line-height: 21px; }
</style>
</head>
<body>

<section class="card card-front" aria-label="Business card front">
  <div class="front-brand">
    <span class="dot"></span>
    <span class="name">CrewSafe Clinics</span>
  </div>
  <p class="front-url">www.<span class="u-sky">crewsafe</span><span class="u-indigo">clinics</span>.com</p>
</section>

<section class="card card-back" aria-label="Business card back">
  <div class="stripes">
    <span class="stripe stripe-amber"></span>
    <span class="stripe stripe-navy"></span>
    <span class="stripe stripe-sky"></span>
  </div>

  <div class="back-brand">
    <span class="dot"></span>
    <span class="name">CrewSafe Clinics</span>
  </div>

  <div class="person">
    <h1 class="person-name">Dana Reyes</h1>
    <p class="person-title">Senior Doctor</p>
  </div>

  <ul class="contacts">
    <li>
      <svg viewBox="0 0 16 16" aria-hidden="true"><path fill="#2a9fd8" d="M2 5c0-2 2-3 6-3s6 1 6 3v1h-3V5H5v1H2zM4 7h8l2 6H2z"/></svg>
      555-010-2480
    </li>
    <li>
      <svg viewBox="0 0 16 16" aria-hidden="true"><rect x="1" y="3" width="14" height="10" fill="#2e2f7a"/><path d="M1 3l7 6 7-6" fill="none" stroke="#f6f6f4" stroke-width="1.4"/></svg>
      dana@crewsafe.com
    </li>
    <li>
      <svg viewBox="0 0 16 16" aria-hidden="true"><circle cx="8" cy="8" r="6.5" fill="#f0a833"/><path d="M1.5 8h13M8 1.5v13M3 4.5h10M3 11.5h10" stroke="#f6f6f4" stroke-width="0.9"/></svg>
      www.crewsafe.com
    </li>
  </ul>

  <div class="address">
    <svg viewBox="0 0 14 18" aria-hidden="true"><path fill="#f0a833" d="M7 0a6 6 0 0 1 6 6c0 4.5-6 12-6 12S1 10.5 1 6a6 6 0 0 1 6-6z"/><circle cx="7" cy="6" r="2.3" fill="#f6f6f4"/></svg>
    <p>48 Harbor Lane, Suite 210<br>Portside, State 54321</p>
  </div>
</section>

</body>
</html>
```